Brightway Carpet and Tile cleaning Business card Design

I need a design that has the same feel as my van.
i would also like a prominent "Review us on facebook" somewhere, but not that it makes it look silly.
I would like the card to have a little bit of grey or black in the design as well.

It will need contact details
phone: 0455 817264
email: rkbrightwayclean@mailbox-example.com
website: www.brightwaycarpetandtilecleaning-example.com.au
facebook: /brightwaycarpetandtilecleaning

Industry/Entity Type

Business

Contact Information for Business Card

Phone number 0455817264
Email rkbrightwayclean@mailbox-example.com
Website www.brightwaycarpetandtilecleaning-example.com.au
Facebook/brightwaycarpetandtilecleaning

Colors
000000

Requirements
Must have
• Same feel as my van
• I want the card to stand out from the crowd
Nice to have
• Maybe include a tiny bit of a third colour? Grey's,blacks, orange?

```html
<!DOCTYPE html>
<html lang="en">
<head>
<meta charset="utf-8">
<title>Brightway Carpet and Tile Cleaning – Business Card</title>
<link href="https://fonts.googleapis.com/css2?family=Arimo:wght@400;700&display=swap" rel="stylesheet">
<style>
  :root {
    --stage: #e6e7e9;
    --card-dark: #3b3b3d;
    --card-light: #ffffff;
    --brand-blue: #1ba3dc;
    --band-grey: #3f3f41;
    --ink: #2b2b2b;
    --white: #ffffff;
  }
  * { box-sizing: border-box; margin: 0; padding: 0; }
  html, body {
    width: 1200px; height: 900px; overflow: hidden;
    background: var(--stage);
    font-family: "Arimo", Arial, sans-serif;
  }
  .stage { position: relative; width: 1200px; height: 900px; }

  .card {
    position: absolute;
    width: 620px; height: 354px;
    border-radius: 26px;
    overflow: hidden;
    box-shadow: 0 10px 28px rgba(0,0,0,.22);
  }

  /* Brand lock-up (text only) */
  .brand { position: absolute; display: flex; align-items: center; gap: 12px; }
  .brand__dot { width: 16px; height: 16px; border-radius: 50%; background: var(--brand-blue); flex: none; }
  .brand__text { color: var(--brand-blue); font-weight: 700; line-height: 1.1; }
  .brand__name { display: block; }
  .brand__tag { display: block; font-size: 14px; letter-spacing: 2px; text-transform: uppercase; }

  /* Back side */
  .card--back { left: 110px; top: 80px; background: var(--card-dark); }
  .card--back .brand { left: 0; right: 0; top: 118px; justify-content: center; }
  .card--back .brand__name { font-size: 44px; }
  .review-cta {
    position: absolute; left: 0; right: 0; bottom: 62px;
    text-align: center; color: var(--white);
    font-weight: 700; font-size: 19px; letter-spacing: 2.5px;
  }

  /* Front side */
  .card--front { left: 470px; top: 470px; background: var(--card-light); }
  .card__shapes { position: absolute; inset: 0; }
  .card--front .brand { left: 44px; top: 92px; }
  .card--front .brand__name { font-size: 38px; }
  .card--front .brand__tag { font-size: 13px; }
  .holder-name {
    position: absolute; right: 52px; top: 56px;
    color: var(--brand-blue); font-size: 26px; font-weight: 400; letter-spacing: 1px;
  }
  .contact-list {
    position: absolute; left: 44px; top: 228px;
    list-style: none; color: var(--ink); font-size: 14.5px;
  }
  .contact-list li { display: flex; align-items: center; gap: 10px; height: 19px; }
  .contact-list svg { width: 12px; height: 12px; flex: none; }
</style>
</head>
<body>
<main class="stage">

  <section class="card card--back" aria-label="Business card back">
    <div class="brand">
      <span class="brand__dot"></span>
      <span class="brand__text">
        <span class="brand__name">Brightway</span>
        <span class="brand__tag">Carpet &amp; Tile Cleaning</span>
      </span>
    </div>
    <p class="review-cta">REVIEW US ON FRIENDSPACE</p>
  </section>

  <section class="card card--front" aria-label="Business card front">
    <svg class="card__shapes" viewBox="0 0 620 354" aria-hidden="true">
      <line x1="590" y1="82" x2="40" y2="222" stroke="#2b2b2b" stroke-width="1.5"/>
      <polygon points="0,332 470,306 470,318 0,346" fill="var(--brand-blue)"/>
      <polygon points="500,196 620,174 620,300 470,318 470,236" fill="var(--band-grey)"/>
    </svg>
    <div class="brand">
      <span class="brand__dot"></span>
      <span class="brand__text">
        <span class="brand__name">Brightway</span>
        <span class="brand__tag">Carpet &amp; Tile Cleaning</span>
      </span>
    </div>
    <p class="holder-name">MARCUS</p>
    <ul class="contact-list">
      <li>
        <svg viewBox="0 0 12 12"><path d="M2 1l2 0 1 3-1.5 1a6 6 0 0 0 3 3L7.5 6.5l3 1v2a1.5 1.5 0 0 1-1.5 1.5A9 9 0 0 1 .5 2.5 1.5 1.5 0 0 1 2 1z" fill="var(--brand-blue)"/></svg>
        0455 817264
      </li>
      <li>
        <svg viewBox="0 0 12 12"><rect x="1" y="2.5" width="10" height="7" fill="none" stroke="var(--brand-blue)" stroke-width="1.2"/><path d="M1 2.5l5 4 5-4" fill="none" stroke="var(--brand-blue)" stroke-width="1.2"/></svg>
        rkbrightwayclean@mailbox-example.com
      </li>
      <li>
        <svg viewBox="0 0 12 12"><circle cx="6" cy="6" r="5" fill="none" stroke="var(--brand-blue)" stroke-width="1.1"/><ellipse cx="6" cy="6" rx="2.2" ry="5" fill="none" stroke="var(--brand-blue)" stroke-width="1"/><line x1="1" y1="6" x2="11" y2="6" stroke="var(--brand-blue)" stroke-width="1"/></svg>
        www.brightwaycarpetandtilecleaning-example.com.au
      </li>
      <li>
        <svg viewBox="0 0 12 12"><rect x="2" y="2" width="8" height="8" fill="var(--brand-blue)"/></svg>
        Friendspace/brightwaycarpetandtilecleaning
      </li>
    </ul>
  </section>

</main>
</body>
</html>
```